brqnal new business card design project

we need a new business card design. you can view info about us @ brqnal-example.com. i have attached an example of our previous card with our previous name that we no longer use. We really liked the design, colors etc. look below to see more info about this project. it asks for a limited number of words. please see our website for more info about our compnay.

Target Market(s)

law enforcement

Contact Information for Business Card

i have uploaded an example of what we used before that we liked.

Font styles to use
Serif

```html
<!DOCTYPE html>
<html lang="en">
<head>
<meta charset="utf-8">
<title>brqnal business card</title>
<link href="https://fonts.googleapis.com/css2?family=Open+Sans:wght@300;400;700&display=swap" rel="stylesheet">
<style>
  :root {
    --page: #2b2e33;
    --paper: #ffffff;
    --navy: #0b1d2c;
    --navy-deep: #061420;
    --steel: #1b4a66;
    --steel-light: #2c6585;
    --frame: #2a6fa8;
    --ink: #1a1a1a;
    --grey: #8a8a8a;
    --light: #e8edf2;
  }
  * { margin: 0; padding: 0; box-sizing: border-box; }
  html, body { width: 1200px; height: 900px; overflow: hidden; }
  body {
    background: var(--page);
    font-family: "Open Sans", sans-serif;
    display: flex; flex-direction: column; align-items: center; justify-content: center; gap: 60px;
  }
  .card {
    position: relative; width: 560px; height: 320px; border-radius: 26px; overflow: hidden;
    box-shadow: 0 14px 30px rgba(0,0,0,.45);
  }
  .card-front { background: var(--paper); }
  .front-wave { position: absolute; inset: 0; }
  .wordmark { font-weight: 300; letter-spacing: 4px; line-height: 1; white-space: nowrap; }
  .front-brand { position: absolute; left: 36px; top: 64px; }
  .front-brand .wordmark { font-size: 54px; color: var(--ink); }
  .rule { height: 1px; margin-top: 12px; }
  .front-brand .rule { width: 240px; background: linear-gradient(90deg, var(--grey), transparent); }
  .front-brand .url { margin-top: 10px; font-size: 15px; color: var(--grey); letter-spacing: 1px; padding-left: 12px; white-space: nowrap; }
  .person { position: absolute; left: 352px; top: 96px; color: var(--paper); white-space: nowrap; }
  .person .name { font-weight: 700; font-size: 21px; line-height: 1.2; }
  .person .role { font-size: 11px; font-weight: 300; margin-top: 3px; }
  .person .role-rule { width: 70px; height: 1px; background: var(--light); margin-top: 8px; }

  .card-back { background: radial-gradient(ellipse at 40% 30%, var(--navy), var(--navy-deep)); }
  .back-frame { position: absolute; inset: 12px; border: 3px solid var(--frame); border-radius: 18px; }
  .back-brand { position: absolute; left: 0; right: 0; top: 58px; text-align: center; }
  .back-brand .wordmark { font-size: 58px; color: var(--light); }
  .back-brand .rule { width: 300px; margin: 12px auto 0; background: linear-gradient(90deg, transparent, var(--grey), transparent); }
  .contacts { position: absolute; left: 70px; top: 180px; list-style: none; color: var(--light); font-size: 15px; }
  .contacts li { display: flex; align-items: center; gap: 10px; margin-bottom: 10px; white-space: nowrap; }
  .contacts svg { width: 16px; height: 16px; flex: none; }
  .contacts .pair { display: flex; gap: 28px; }
  .contacts .pair span { display: flex; align-items: center; gap: 10px; }
</style>
</head>
<body>
  <section class="card card-front">
    <svg class="front-wave" viewBox="0 0 560 320" aria-hidden="true">
      <defs>
        <linearGradient id="waveFill" x1="0" y1="0" x2="1" y2="1">
          <stop offset="0" stop-color="#1b4a66"/>
          <stop offset="1" stop-color="#0c2436"/>
        </linearGradient>
      </defs>
      <path d="M290 0 C 350 40, 360 200, 220 320 L560 320 L560 0 Z" fill="url(#waveFill)"/>
      <path d="M350 320 C 405 250, 415 160, 390 80 C 455 160, 475 250, 465 320 Z" fill="#2c6585" opacity=".35"/>
    </svg>
    <div class="front-brand">
      <div class="wordmark">BRQNAL</div>
      <div class="rule"></div>
      <div class="url">www.brqnal-example.com</div>
    </div>
    <div class="person">
      <div class="name">Dorian Keller</div>
      <div class="role">Founder/chief Executive Officer</div>
      <div class="role-rule"></div>
    </div>
  </section>

  <section class="card card-back">
    <div class="back-frame"></div>
    <div class="back-brand">
      <div class="wordmark">BRQNAL</div>
      <div class="rule"></div>
    </div>
    <ul class="contacts">
      <li>
        <svg viewBox="0 0 16 16"><path d="M8 1a5 5 0 0 0-5 5c0 4 5 9 5 9s5-5 5-9a5 5 0 0 0-5-5zm0 7a2 2 0 1 1 0-4 2 2 0 0 1 0 4z" fill="#c9d3dc"/></svg>
        4120 Larkspur Lane, Avonmere, TX 70000
      </li>
      <li class="pair">
        <span>
          <svg viewBox="0 0 16 16"><path d="M4 1l3 3-2 2c1 2 3 4 5 5l2-2 3 3-2 3C7 15 1 9 1 3z" fill="#c9d3dc"/></svg>
          555.014.2290
        </span>
        <span>
          <svg viewBox="0 0 16 16"><rect x="1" y="3" width="14" height="10" rx="1" fill="#c9d3dc"/><path d="M1 4l7 5 7-5" stroke="#0b1d2c" stroke-width="1.4" fill="none"/></svg>
          info@brqnal-example.com
        </span>
      </li>
      <li>
        <svg viewBox="0 0 16 16"><circle cx="8" cy="8" r="6.5" fill="none" stroke="#c9d3dc" stroke-width="1.4"/><path d="M1.5 8h13M8 1.5c3 3 3 10 0 13M8 1.5c-3 3-3 10 0 13" stroke="#c9d3dc" stroke-width="1.1" fill="none"/></svg>
        www.brqnal-example.com
      </li>
    </ul>
  </section>
</body>
</html>
```